Stationery Design Project

Please create a custom Stationery Design for Pinecrest Dwellings. The logo is attached to this brief.

Please Include:
- Letterhead
- With Compliments slip
- Envelope

Please also see open Business Card project: http://briefs.sketchvault.example/task.aspx?id=517290

Industry/Entity Type

Business

```html
<!DOCTYPE html>
<html lang="en">
<head>
<meta charset="utf-8">
<title>Pinecrest Dwellings — Stationery</title>
<link href="https://fonts.googleapis.com/css2?family=Source+Sans+3:wght@400;600&display=swap" rel="stylesheet">
<style>
  :root {
    --backdrop: #5f5f5f;
    --paper: #ffffff;
    --brand-blue: #0d6dbd;
    --brand-green: #8cc63f;
    --brand-yellow: #f7c81e;
    --ink: #4a4a4a;
    --rule: #b9b9b9;
    --mark-tint: #e3e3e3;
    --shadow: 0 3px 8px rgba(0,0,0,.45);
  }
  * { box-sizing: border-box; margin: 0; padding: 0; }
  html, body { width: 1200px; height: 640px; overflow: hidden; }
  body {
    background: var(--backdrop);
    font-family: "Source Sans 3", "Myriad Pro", Arial, sans-serif;
    position: relative;
  }
  .sheet {
    position: absolute;
    background: var(--paper);
    box-shadow: var(--shadow);
    overflow: hidden;
  }
  .letterhead { left: 72px; top: 58px; width: 384px; height: 530px; }
  .envelope-front { left: 525px; top: 42px; width: 446px; height: 178px; }
  .envelope-back { left: 724px; top: 246px; width: 446px; height: 178px; }
  .comp-slip { left: 550px; top: 450px; width: 346px; height: 154px; }

  .brand-band {
    position: absolute; left: 0; bottom: 0; width: 100%; height: 6px; display: block;
  }

  .wordmark {
    position: absolute;
    display: flex; flex-direction: column; align-items: center;
    color: var(--brand-blue); font-weight: 600; text-transform: uppercase;
    line-height: 1.05; letter-spacing: .04em;
  }
  .wordmark .dot {
    border-radius: 50%; background: var(--brand-yellow); margin-bottom: 4px;
  }
  .letterhead .wordmark { left: 50%; top: 28px; transform: translateX(-50%); font-size: 14px; }
  .letterhead .wordmark .dot { width: 22px; height: 22px; }
  .envelope-front .wordmark { left: 26px; top: 114px; font-size: 11px; }
  .envelope-front .wordmark .dot { width: 18px; height: 18px; }
  .comp-slip .wordmark { left: 22px; top: 96px; font-size: 10px; }
  .comp-slip .wordmark .dot { width: 16px; height: 16px; }

  .mark-tint {
    position: absolute; border-radius: 50%; background: var(--mark-tint);
  }
  .letterhead .mark-tint { width: 150px; height: 150px; right: 14px; bottom: 40px; }
  .envelope-front .mark-tint { width: 104px; height: 104px; right: 24px; top: 48px; }
  .comp-slip .mark-tint { width: 82px; height: 82px; right: 22px; top: 54px; }

  .address {
    position: absolute; font-size: 5.5px; color: var(--ink); line-height: 1.45;
  }
  .envelope-front .address { left: 126px; top: 148px; border-left: 1px solid var(--rule); padding-left: 5px; }
  .comp-slip .address { left: 100px; top: 126px; border-left: 1px solid var(--rule); padding-left: 4px; font-size: 5px; }
  .letterhead .address { left: 48px; top: 490px; width: 90px; text-align: right; }

  .contacts {
    position: absolute; font-size: 5.5px; color: var(--ink); line-height: 1.6;
    border-left: 1px solid var(--rule); padding-left: 4px;
  }
  .contacts li { list-style: none; display: flex; align-items: center; gap: 3px; }
  .contacts .icon {
    width: 6px; height: 6px; background: var(--brand-blue); border-radius: 1px; display: inline-block;
  }
  .letterhead .contacts { left: 143px; top: 488px; font-size: 6px; }
  .comp-slip .contacts { left: 180px; top: 126px; font-size: 5px; }

  .comp-title {
    position: absolute; right: 20px; top: 12px;
    color: var(--brand-blue); font-size: 13px; font-weight: 400;
  }

  .flap { position: absolute; left: 0; top: 0; width: 446px; height: 60px; }
  .envelope-back .wordmark-seal {
    position: absolute; left: 50%; top: 14px; transform: translateX(-50%);
    width: 28px; height: 28px; border-radius: 50%; background: var(--brand-yellow);
  }
</style>
</head>
<body>

  <section class="sheet letterhead" aria-label="Letterhead">
    <div class="wordmark"><span class="dot"></span><span>Pinecrest</span><span>Dwellings</span></div>
    <div class="mark-tint"></div>
    <p class="address">12 Alder Court<br>Meadowbank Business Park, City Name</p>
    <ul class="contacts">
      <li><span class="icon"></span>020 7946 0321</li>
      <li><span class="icon"></span>www.pinecrest.example</li>
    </ul>
    <svg class="brand-band" viewBox="0 0 384 6" preserveAspectRatio="none">
      <polygon points="0,0 240,0 237,6 0,6" fill="var(--brand-green)"/>
      <polygon points="244,0 384,0 384,6 241,6" fill="var(--brand-blue)"/>
    </svg>
  </section>

  <section class="sheet envelope-front" aria-label="Envelope front">
    <div class="mark-tint"></div>
    <div class="wordmark"><span class="dot"></span><span>Pinecrest</span><span>Dwellings</span></div>
    <p class="address">12 Alder Court, Address Line<br>Meadowbank Business Park, City Name</p>
    <svg class="brand-band" viewBox="0 0 446 7" preserveAspectRatio="none" style="height:7px">
      <polygon points="0,0 288,0 285,7 0,7" fill="var(--brand-green)"/>
      <polygon points="292,0 446,0 446,7 289,7" fill="var(--brand-blue)"/>
    </svg>
  </section>

  <section class="sheet envelope-back" aria-label="Envelope back">
    <svg class="flap" viewBox="0 0 446 60">
      <path d="M1 0 V38 Q1 50 14 50 H432 Q445 50 445 38 V0" fill="none" stroke="var(--rule)" stroke-width="1"/>
    </svg>
    <span class="wordmark-seal"></span>
  </section>

  <section class="sheet comp-slip" aria-label="With compliments slip">
    <h2 class="comp-title">With Compliments</h2>
    <div class="mark-tint"></div>
    <div class="wordmark"><span class="dot"></span><span>Pinecrest</span><span>Dwellings</span></div>
    <p class="address">12 Alder Court, Address Line<br>Meadowbank Business Park, City Name</p>
    <ul class="contacts">
      <li><span class="icon"></span>020 7946 0321</li>
      <li><span class="icon"></span>www.pinecrest.example</li>
    </ul>
    <svg class="brand-band" viewBox="0 0 346 6" preserveAspectRatio="none">
      <polygon points="0,0 224,0 221,6 0,6" fill="var(--brand-green)"/>
      <polygon points="228,0 346,0 346,6 225,6" fill="var(--brand-blue)"/>
    </svg>
  </section>

</body>
</html>
```